Window and GutterCleaning Flyer A5 size double sided.

We need a double sided A5 flyer. Side 1, is for window cleaning, side 2 is for gutter cleaning. Licensed by Borough of Marlow Council.
Phone number 0800 473 1926.
Business address 17 Fallowmere Close, North Brack Edinburgh EH31 4LP.
www.clearpane-hub-services.com
We use a LoftEye Gutter inspection Cam to view your gutters first to see if they need doing.
Window cleaning ; Professional window cleaning services, what we offer, water fed pole window cleaning able to reach windows up to 60 feet.
Conservatory cleaning.
Conservatory roof cleaning.
Fascias & Soffits cleaning.
Excellent Customer Service.
Target Market(s)
domestic houses
Industry/Entity Type
window cleaning
Look and feel
Each slider illustrates characteristics of the customer's brand and the style your logo design should communicate.

```html
<!DOCTYPE html>
<html lang="en">
<head>
<meta charset="utf-8">
<title>ClearPane Hub Services – Window &amp; Gutter Cleaning Flyer</title>
<link rel="stylesheet" href="https://fonts.googleapis.com/css2?family=Montserrat:wght@400;500;600;700;800;900&display=swap">
<style>
  :root{
    --navy:#2e2b6e;
    --navy-deep:#262362;
    --sky:#8fbbe8;
    --sky-soft:#b9d5f2;
    --ink:#1f1d4d;
    --paper:#ffffff;
    --gold:#d9a520;
    --gold-light:#f3d774;
    --stage:#2f2f2f;
  }
  *{margin:0;padding:0;box-sizing:border-box}
  html,body{width:889px;height:1200px;overflow:hidden;background:var(--stage)}
  body{position:relative;font-family:"Montserrat",Arial,sans-serif;color:var(--ink)}

  .flyer{position:absolute;top:306px;width:660px;height:925px;background:var(--paper);overflow:hidden;transform:scale(.636);transform-origin:0 0;box-shadow:0 0 20px rgba(0,0,0,.5)}
  .flyer--window{left:16px}
  .flyer--gutter{left:453px}
  .backdrop{position:absolute;inset:0}

  .brand{position:absolute;left:30px;top:118px;display:flex;align-items:center;gap:10px}
  .brand-mark{width:18px;height:18px;background:var(--sky)}
  .brand-name{font-weight:800;font-size:24px;line-height:1;color:var(--paper)}
  .brand-city{position:absolute;left:58px;top:152px;font-size:12px;font-weight:600;color:var(--sky-soft)}

  .headline{position:absolute;left:28px;font-weight:900;font-size:48px;line-height:46px;color:var(--navy)}
  .headline .accent{color:var(--sky)}
  .flyer--window .headline{top:280px}
  .flyer--gutter .headline{top:300px}

  .intro{position:absolute;left:29px;font-size:14.5px;font-weight:500;line-height:19px;color:var(--ink)}
  .flyer--window .intro{top:442px;width:600px}
  .flyer--gutter .intro{top:412px;width:470px}

  .section-title{font-weight:800;font-size:21px;line-height:26px;color:var(--navy)}
  .services{position:absolute;width:250px}
  .flyer--window .services{left:40px;top:518px}
  .flyer--gutter .services{left:28px;top:494px;width:265px;height:345px;background:var(--sky);padding:20px 14px 0 12px}
  .service-list{list-style:none;margin-top:8px}
  .service-list li{display:flex;align-items:center;gap:14px;padding:4px 0;border-bottom:1px dashed rgba(46,43,110,.35);min-height:39px}
  .service-list li:last-child{border-bottom:none}
  .service-icon{flex:0 0 26px;width:26px;height:26px}
  .service-name{font-weight:600;font-size:14px;line-height:15px;color:var(--navy);text-transform:uppercase}

  .divider{position:absolute;left:290px;top:520px;width:2px;height:295px;background:var(--sky)}
  .details{position:absolute;left:306px;top:518px;width:330px}
  .details p{font-size:11.5px;line-height:13.5px;color:var(--ink)}
  .benefits-bar{margin-top:8px;background:var(--sky);padding:4px 8px;font-weight:800;font-size:11.5px;color:var(--navy);text-transform:uppercase}
  .benefit-list{list-style:none;margin-top:5px}
  .benefit-list li{display:flex;align-items:center;gap:5px;font-size:11px;font-weight:600;line-height:16.5px}
  .tick{width:10px;height:10px;flex:0 0 10px}
  .how-title{margin-top:9px;font-weight:800;font-size:13.5px;color:var(--navy);text-transform:uppercase}
  .how-title + p{margin-top:3px}

  .article{position:absolute;left:307px;top:500px;width:330px}
  .article p{font-size:11px;line-height:12.5px;text-align:justify;color:var(--ink);margin-bottom:11px}

  .badge{position:absolute;left:100px;top:772px;width:126px;height:126px}
  .website{position:absolute;display:flex;align-items:center;gap:8px;font-weight:700;font-size:12.5px;color:var(--navy)}
  .flyer--window .website{left:32px;top:899px}
  .flyer--gutter .website{left:32px;top:812px}

  .contact{position:absolute;font-style:normal;color:var(--paper)}
  .flyer--window .contact{left:340px;top:840px}
  .flyer--gutter .contact{left:30px;top:846px}
  .contact-row{display:flex;align-items:center;gap:8px}
  .phone{font-weight:800;font-size:23px;line-height:27px}
  .contact-small{font-size:11.5px;font-weight:500;line-height:13px}
  .contact-icon{width:13px;height:13px;flex:0 0 13px}
</style>
</head>
<body>

<!-- Side 1: window cleaning -->
<main class="flyer flyer--window">
  <svg class="backdrop" width="660" height="925" viewBox="0 0 660 925">
    <defs>
      <linearGradient id="windowPhotoTone" x1="0" y1="0" x2="1" y2="1">
        <stop offset="0" stop-color="#3d3a6c"/>
        <stop offset=".35" stop-color="#6f8a5a"/>
        <stop offset=".7" stop-color="#c9c4b0"/>
        <stop offset="1" stop-color="#e9e4da"/>
      </linearGradient>
      <linearGradient id="glassTone" x1="0" y1="0" x2="1" y2="1">
        <stop offset="0" stop-color="#1f2f55"/>
        <stop offset=".6" stop-color="#4f8fc4"/>
        <stop offset="1" stop-color="#a9d3f0"/>
      </linearGradient>
    </defs>
    <rect x="220" y="0" width="440" height="400" fill="url(#windowPhotoTone)" role="img" aria-label="Photo of a woman in yellow gloves cleaning a window, with a gutter inspection camera tablet"/>
    <polygon points="0,0 250,0 225,250 0,250" fill="var(--navy)"/>
    <polygon points="0,246 420,206 420,216 0,256" fill="var(--sky)"/>
    <polygon points="0,256 420,216 420,360 660,400 660,925 0,925" fill="var(--paper)"/>
    <circle cx="430" cy="313" r="86" fill="var(--sky)"/>
    <circle cx="430" cy="313" r="80" fill="url(#glassTone)" role="img" aria-label="Close-up photo of a squeegee on window glass"/>
    <polygon points="330,831 660,831 660,925 262,925" fill="var(--navy-deep)"/>
  </svg>

  <div class="brand"><span class="brand-mark"></span><span class="brand-name">CLEARPANE HUB</span></div>
  <div class="brand-city">Edinburgh</div>

  <h1 class="headline">CLEARPANE<br><span class="accent">WINDOW</span><br>CLEANING</h1>

  <p class="intro">We use a LoftEye Gutter inspection Cam to view your gutters first to see if they need doing. Window cleaning ; Professional window cleaning services, what we offer, water fed pole window cleaning able to reach windows up to 60 feet.</p>

  <section class="services">
    <h2 class="section-title">OUR SERVICES</h2>
    <ul class="service-list">
      <li><svg class="service-icon" viewBox="0 0 32 32"><circle cx="16" cy="16" r="15" fill="var(--sky-soft)"/><rect x="9" y="8" width="14" height="16" rx="2" fill="none" stroke="var(--navy)" stroke-width="2"/><line x1="16" y1="8" x2="16" y2="24" stroke="var(--navy)" stroke-width="1.5"/></svg><span class="service-name">Window Cleaning</span></li>
      <li><svg class="service-icon" viewBox="0 0 32 32"><circle cx="16" cy="16" r="15" fill="var(--sky-soft)"/><circle cx="16" cy="16" r="8" fill="none" stroke="var(--navy)" stroke-width="2"/><line x1="12" y1="20" x2="20" y2="12" stroke="var(--navy)" stroke-width="2"/></svg><span class="service-name">What We Offer</span></li>
      <li><svg class="service-icon" viewBox="0 0 32 32"><circle cx="16" cy="16" r="15" fill="var(--sky-soft)"/><path d="M8 18 L16 10 L24 18 V24 H8 Z" fill="none" stroke="var(--navy)" stroke-width="2"/></svg><span class="service-name">Conservatory Roof<br>Cleaning</span></li>
      <li><svg class="service-icon" viewBox="0 0 32 32"><circle cx="16" cy="16" r="15" fill="var(--sky-soft)"/><path d="M7 12 H25 L22 20 H10 Z" fill="none" stroke="var(--navy)" stroke-width="2"/><line x1="12" y1="22" x2="12" y2="26" stroke="var(--navy)" stroke-width="2"/></svg><span class="service-name">Fascias &amp; Soffits<br>Cleaning</span></li>
      <li><svg class="service-icon" viewBox="0 0 32 32"><circle cx="16" cy="16" r="15" fill="var(--sky-soft)"/><polygon points="16,7 18.5,13 25,13.5 20,17.5 21.5,24 16,20.5 10.5,24 12,17.5 7,13.5 13.5,13" fill="none" stroke="var(--navy)" stroke-width="1.8"/></svg><span class="service-name">Excellent Customer<br>Service</span></li>
    </ul>
  </section>

  <div class="divider"></div>

  <section class="details">
    <h2 class="section-title">WINDOW CLEANING</h2>
    <p>Regular window cleaning helps to avoid the build-up of dirt and residue on the glass, meaning more light can get into your home or premises and can also improve its external appearance.</p>
    <div class="benefits-bar">Benefits of pure hot water system</div>
    <ul class="benefit-list">
      <li><svg class="tick" viewBox="0 0 12 12"><path d="M1 6 L4.5 9.5 L11 2" fill="none" stroke="var(--sky)" stroke-width="2"/></svg>Better cleaning results</li>
      <li><svg class="tick" viewBox="0 0 12 12"><path d="M1 6 L4.5 9.5 L11 2" fill="none" stroke="var(--sky)" stroke-width="2"/></svg>Frames and sills are cleaned at the same time</li>
      <li><svg class="tick" viewBox="0 0 12 12"><path d="M1 6 L4.5 9.5 L11 2" fill="none" stroke="var(--sky)" stroke-width="2"/></svg>Reduced disturbance to you and your garden</li>
      <li><svg class="tick" viewBox="0 0 12 12"><path d="M1 6 L4.5 9.5 L11 2" fill="none" stroke="var(--sky)" stroke-width="2"/></svg>Increased privacy</li>
      <li><svg class="tick" viewBox="0 0 12 12"><path d="M1 6 L4.5 9.5 L11 2" fill="none" stroke="var(--sky)" stroke-width="2"/></svg>No need to move your car out the driveway!</li>
    </ul>
    <h3 class="how-title">So, how does it work?</h3>
    <p>Ordinary tap water is full of sediments and minerals and whilst OK to drink, it's these impurities that cause spotting and streaking when tap water is left to dry on a surface.</p>
  </section>

  <svg class="badge" viewBox="0 0 130 130" aria-hidden="true">
    <circle cx="65" cy="65" r="62" fill="var(--gold)"/>
    <circle cx="65" cy="65" r="46" fill="var(--gold-light)"/>
  </svg>

  <div class="website">
    <svg class="contact-icon" viewBox="0 0 16 16"><circle cx="8" cy="8" r="7" fill="none" stroke="var(--navy)" stroke-width="1.5"/><ellipse cx="8" cy="8" rx="3" ry="7" fill="none" stroke="var(--navy)" stroke-width="1.2"/><line x1="1" y1="8" x2="15" y2="8" stroke="var(--navy)" stroke-width="1.2"/></svg>
    clearpane-hub-services.com
  </div>

  <address class="contact">
    <div class="contact-row phone">
      <svg class="contact-icon" viewBox="0 0 16 16"><path d="M3 1 L6 1 L7 5 L5 6.5 C6 9 7 10 9.5 11 L11 9 L15 10 L15 13 C15 14 14 15 13 15 C7 15 1 9 1 3 C1 2 2 1 3 1 Z" fill="none" stroke="var(--paper)" stroke-width="1.4"/></svg>
      0800 473 1926
    </div>
    <div class="contact-row contact-small">
      <svg class="contact-icon" viewBox="0 0 16 16"><rect x="1" y="3" width="14" height="10" fill="none" stroke="var(--paper)" stroke-width="1.4"/><path d="M1 3 L8 9 L15 3" fill="none" stroke="var(--paper)" stroke-width="1.4"/></svg>
      info@clearpane-hub-services.com
    </div>
    <div class="contact-row contact-small" style="margin-top:3px">
      <svg class="contact-icon" viewBox="0 0 16 16"><path d="M8 15 C4 10 3 8 3 6 A5 5 0 0 1 13 6 C13 8 12 10 8 15 Z" fill="none" stroke="var(--paper)" stroke-width="1.4"/><circle cx="8" cy="6" r="1.8" fill="var(--paper)"/></svg>
      <span>ClearPane Hub Services 17 Fallowmere Close<br>North Brack Edinburgh EH31 4LP</span>
    </div>
  </address>
</main>

<!-- Side 2: gutter cleaning -->
<main class="flyer flyer--gutter">
  <svg class="backdrop" width="660" height="925" viewBox="0 0 660 925">
    <defs>
      <linearGradient id="gutterPhotoTone" x1="0" y1="0" x2="1" y2="1">
        <stop offset="0" stop-color="#3a376c"/>
        <stop offset=".4" stop-color="#7a7894"/>
        <stop offset=".7" stop-color="#b58a4a"/>
        <stop offset="1" stop-color="#d8d6d2"/>
      </linearGradient>
      <linearGradient id="gutterInsetTone" x1="0" y1="0" x2="1" y2="1">
        <stop offset="0" stop-color="#5c6470"/>
        <stop offset="1" stop-color="#d8dadc"/>
      </linearGradient>
      <linearGradient id="downpipeTone" x1="0" y1="0" x2="1" y2="1">
        <stop offset="0" stop-color="#4e7a3c"/>
        <stop offset="1" stop-color="#8aa4b8"/>
      </linearGradient>
      <linearGradient id="roofSkyTone" x1="0" y1="0" x2="0" y2="1">
        <stop offset="0" stop-color="#d8ecfa"/>
        <stop offset=".6" stop-color="#5a9ad6"/>
        <stop offset="1" stop-color="#8a5a48"/>
      </linearGradient>
    </defs>
    <rect x="0" y="0" width="660" height="300" fill="url(#gutterPhotoTone)" role="img" aria-label="Photo of a gloved hand lifting autumn leaves out of a roof gutter"/>
    <polygon points="0,0 200,0 240,250 0,250" fill="var(--navy)" opacity=".85"/>
    <polygon points="0,244 330,236 330,246 0,254" fill="var(--sky)"/>
    <polygon points="0,254 330,246 500,260 660,290 660,925 0,925" fill="var(--paper)"/>
    <rect x="293" y="790" width="367" height="135" fill="url(#roofSkyTone)" role="img" aria-label="Photo of a man pressure washing a roof under a blue sky"/>
    <circle cx="419" cy="337" r="87" fill="var(--sky)"/>
    <circle cx="419" cy="337" r="81" fill="url(#gutterInsetTone)" role="img" aria-label="Close-up photo of a gutter being cleared with a vacuum hose"/>
    <circle cx="565" cy="385" r="70" fill="var(--sky)"/>
    <circle cx="565" cy="385" r="64" fill="url(#downpipeTone)" role="img" aria-label="Photo of a downpipe on a house wall"/>
    <polygon points="0,839 300,839 395,925 0,925" fill="var(--navy-deep)"/>
  </svg>

  <div class="brand"><span class="brand-mark"></span><span class="brand-name">CLEARPANE HUB</span></div>
  <div class="brand-city">Edinburgh</div>

  <h1 class="headline"><span class="accent">GUTTER</span><br>CLEANING</h1>

  <p class="intro">We offer a high-quality, professional window cleaning service across West Edinburgh. With over 30 years experience, we have built up a reliable and trusted reputation on the west side of Edinburgh.</p>

  <section class="services">
    <h2 class="section-title">OUR SERVICES</h2>
    <ul class="service-list">
      <li><svg class="service-icon" viewBox="0 0 32 32"><circle cx="16" cy="16" r="15" fill="var(--paper)"/><rect x="9" y="8" width="14" height="16" rx="2" fill="none" stroke="var(--navy)" stroke-width="2"/><line x1="16" y1="8" x2="16" y2="24" stroke="var(--navy)" stroke-width="1.5"/></svg><span class="service-name">Window Cleaning</span></li>
      <li><svg class="service-icon" viewBox="0 0 32 32"><circle cx="16" cy="16" r="15" fill="var(--paper)"/><circle cx="16" cy="16" r="8" fill="none" stroke="var(--navy)" stroke-width="2"/><line x1="12" y1="20" x2="20" y2="12" stroke="var(--navy)" stroke-width="2"/></svg><span class="service-name">What We Offer</span></li>
      <li><svg class="service-icon" viewBox="0 0 32 32"><circle cx="16" cy="16" r="15" fill="var(--paper)"/><path d="M8 18 L16 10 L24 18 V24 H8 Z" fill="none" stroke="var(--navy)" stroke-width="2"/></svg><span class="service-name">Conservatory Roof<br>Cleaning</span></li>
      <li><svg class="service-icon" viewBox="0 0 32 32"><circle cx="16" cy="16" r="15" fill="var(--paper)"/><path d="M7 12 H25 L22 20 H10 Z" fill="none" stroke="var(--navy)" stroke-width="2"/><line x1="12" y1="22" x2="12" y2="26" stroke="var(--navy)" stroke-width="2"/></svg><span class="service-name">Fascias &amp; Soffits<br>Cleaning</span></li>
      <li><svg class="service-icon" viewBox="0 0 32 32"><circle cx="16" cy="16" r="15" fill="var(--paper)"/><polygon points="16,7 18.5,13 25,13.5 20,17.5 21.5,24 16,20.5 10.5,24 12,17.5 7,13.5 13.5,13" fill="none" stroke="var(--navy)" stroke-width="1.8"/></svg><span class="service-name">Excellent Customer<br>Service</span></li>
    </ul>
  </section>

  <div class="website">
    <svg class="contact-icon" viewBox="0 0 16 16"><circle cx="8" cy="8" r="7" fill="none" stroke="var(--navy)" stroke-width="1.5"/><ellipse cx="8" cy="8" rx="3" ry="7" fill="none" stroke="var(--navy)" stroke-width="1.2"/><line x1="1" y1="8" x2="15" y2="8" stroke="var(--navy)" stroke-width="1.2"/></svg>
    clearpane-hub-services.com
  </div>

  <section class="article">
    <p>ClearPane Hub Services offer a fast and easy gutter cleaning service on residential and commercial properties.</p>
    <p>Gutters are an important part of your home. Letting your gutters get blocked up can cause damage to your property, so why not set up an annual plan and make sure you don't run into problems when winter comes.</p>
    <p>Over time your gutters will fill up with moss, leaves and other unwanted debris which will affect the appearance of your home. When gutters aren't cleared and emptied on a regular basis they become heavy and risk pulling away from the fascias.</p>
    <p>When gutters are not clear it can also lead to blockages in the gutters and downpipes, which will cause the water to overflow. The water which overflows from the guttering can lead to damp problems and other problems in the structure of your property which can become a costly repair.</p>
  </section>

  <address class="contact">
    <div class="contact-row phone">
      <svg class="contact-icon" viewBox="0 0 16 16"><path d="M3 1 L6 1 L7 5 L5 6.5 C6 9 7 10 9.5 11 L11 9 L15 10 L15 13 C15 14 14 15 13 15 C7 15 1 9 1 3 C1 2 2 1 3 1 Z" fill="none" stroke="var(--paper)" stroke-width="1.4"/></svg>
      0800 473 1926
    </div>
    <div class="contact-row contact-small">
      <svg class="contact-icon" viewBox="0 0 16 16"><rect x="1" y="3" width="14" height="10" fill="none" stroke="var(--paper)" stroke-width="1.4"/><path d="M1 3 L8 9 L15 3" fill="none" stroke="var(--paper)" stroke-width="1.4"/></svg>
      info@clearpane-hub-services.com
    </div>
    <div class="contact-row contact-small" style="margin-top:3px">
      <svg class="contact-icon" viewBox="0 0 16 16"><path d="M8 15 C4 10 3 8 3 6 A5 5 0 0 1 13 6 C13 8 12 10 8 15 Z" fill="none" stroke="var(--paper)" stroke-width="1.4"/><circle cx="8" cy="6" r="1.8" fill="var(--paper)"/></svg>
      <span>ClearPane Hub Services 17 Fallowmere Close<br>North Brack Edinburgh EH31 4LP</span>
    </div>
  </address>
</main>

</body>
</html>
```